Investment company needing business card

We are wanting a business card which looks sharp and easy on the eye. We are thinking of having a business card with the logo embossed on it, to really make it stand out. We will only have a small amount of information of the business card, person's name, position, email address and phone number

Contact Information for Business Card

Danielle Frost
Executive Assistant
+64 21 473 5162
danielf@harwickpartners.co.nz

Requirements
Must have
• Embossed logo
Should not have
• Not to be busy

```html
<!DOCTYPE html>
<html lang="en">
<head>
<meta charset="utf-8">
<title>Harwick Partners – Business Card</title>
<link href="https://fonts.googleapis.com/css2?family=Exo+2:wght@700&family=Lato:wght@400;700&display=swap" rel="stylesheet">
<style>
  :root {
    --backdrop: #e9e7e3;
    --card-white: #ffffff;
    --slate: #5f6062;
    --green: #22b573;
    --ink: #3b3b3d;
  }
  * { margin: 0; padding: 0; box-sizing: border-box; }
  html, body { width: 1200px; height: 900px; overflow: hidden; }
  body {
    background: var(--backdrop);
    position: relative;
    font-family: "Lato", sans-serif;
  }
  .card {
    position: absolute;
    width: 540px;
    height: 310px;
    overflow: hidden;
    box-shadow: 0 6px 18px rgba(0,0,0,0.18);
  }
  .card--back {
    left: 110px; top: 110px;
    background: var(--slate);
    display: flex; align-items: center; justify-content: center;
  }
  .card--front {
    left: 550px; top: 480px;
    background: var(--card-white);
  }
  .brand {
    display: flex; align-items: center; gap: 12px;
    font-family: "Lato", sans-serif;
    font-weight: 700;
    letter-spacing: 0.04em;
    text-transform: uppercase;
  }
  .brand__mark { display: block; }
  .card--back .brand { font-size: 30px; color: var(--card-white); }
  .card--back .brand__mark { width: 34px; height: 34px; background: var(--card-white); }
  .card--front .brand {
    position: absolute; right: 30px; top: 48px;
    font-size: 24px; color: var(--green);
  }
  .card--front .brand__mark { width: 28px; height: 28px; background: var(--slate); }
  .card__wave { position: absolute; inset: 0; width: 100%; height: 100%; }
  .contact {
    position: absolute; left: 44px; top: 128px;
    color: var(--ink);
    z-index: 1;
  }
  .contact__name {
    font-family: "Exo 2", sans-serif;
    font-weight: 700;
    font-size: 21px;
    letter-spacing: 0.03em;
    color: var(--green);
    text-transform: uppercase;
  }
  .contact__role { font-size: 15px; margin-top: 1px; }
  .contact__list { list-style: none; margin-top: 14px; font-size: 15px; }
  .contact__item { display: flex; align-items: center; gap: 8px; margin-bottom: 5px; }
  .contact__icon { width: 13px; height: 13px; fill: var(--green); flex: none; }
</style>
</head>
<body>
  <section class="card card--back" aria-label="Business card, reverse">
    <div class="brand"><span class="brand__mark"></span>Harwick Partners</div>
  </section>

  <section class="card card--front" aria-label="Business card, front">
    <svg class="card__wave" viewBox="0 0 540 310" preserveAspectRatio="none" aria-hidden="true">
      <path d="M0,310 L0,304 C170,302 340,250 540,150 L540,310 Z" fill="var(--slate)"/>
      <path d="M0,280 C130,290 280,262 410,205 C300,272 150,298 0,298 Z" fill="var(--green)"/>
    </svg>

    <div class="brand"><span class="brand__mark"></span>Harwick Partners</div>

    <div class="contact">
      <h1 class="contact__name">Danielle Frost</h1>
      <p class="contact__role">Executive Assistant</p>
      <ul class="contact__list">
        <li class="contact__item">
          <svg class="contact__icon" viewBox="0 0 16 16" aria-hidden="true"><path d="M1 5c0-2 2-3 7-3s7 1 7 3v1h-4V4.5H5V6H1z M3 7h10l1.5 6.5H1.5z"/></svg>
          <span>+64 21 473 5162</span>
        </li>
        <li class="contact__item">
          <svg class="contact__icon" viewBox="0 0 16 16" aria-hidden="true"><path d="M1 3h14v10H1z M2 4l6 5 6-5" stroke="#fff" stroke-width="1.2"/></svg>
          <span>danielf@harwickpartners.co.nz</span>
        </li>
      </ul>
    </div>
  </section>
</body>
</html>
```